Help Give House Painter “Fresh” Website Makeover!

A residential and commercial painting company based in Albuquerque, NM, USA needs a fresh, new, fun, and playful--yet, simple, elegant and professional--website made.

Here is a link to their existing site:

http://corvelcoatings.example/

We want to keep a similar site structure., So the navigation layout will stay the same. However, the video is too small, is too far over in the sidebar, and the overall design is amateur at best. We want something bright, colorful and bold!

We will need a space for the Video above the fold, and there needs to be space in the design for Testimonials, Specials and Images. It’s also very important to have the Pellham Roster awards that you see on his current website.

Please also include somewhere in the Design icons for YouTube, Facebook, Google+ and LinkedIn.

Here are some examples to look at to get your creative juices flowing!

http://brightloombrush.example/

http://www.tkvr.example/

http://www.marblow-tennick.example/

http://www.quarrypages.example/painting-company-niche-website/

http://www.brisklayoutdepot.example/website-templates/painting-company-website-template-53817.html

We have accounts at both lumavault.example and pixaroo.example. If you use placeholder images from there, that's fine. We can buy the images when and if your design is selected.

Target Market(s)

The audience is the average middle class homeowner to higher upper class. This should appeal to families, couples, and singles who own a home.

Industry/Entity Type

Residential

Font styles to use
Sans Serif

Requirements
Must have
• - - Lots of color! It's a site about painting homes. People like a variety of colors. Bring out your inner artist, and get bold with your colors!

- - A video place holder. As you can see, there is a video on the existing site, but it's small and hidden. Make it big and put it top left, or in the center.

- -Detailed and organized PSD structure. We're going to turn your design into a website, and to make that work soothly, we ask that you organize you PSD well: name your layers, keep things separated, group and ungroup as necessary, etc.

- A sidebar that goes down the right side of an interior page. We need a homepage, and also one [1] interior page template. We don't need you to make a design for each page. Just the homepage, followed by a simple interior page design that requires only the header/navigation, and a sidebar down the right side.
Should not have
• - Coding. This is a design project only.

```html
<!DOCTYPE html>
<html lang="en">
<head>
<meta charset="utf-8">
<title>Corvel Coatings — Residential &amp; Commercial Painting</title>
<link href="https://fonts.googleapis.com/css2?family=Lato:ital,wght@0,400;0,700;0,900;1,400;1,700;1,900&family=Oswald:wght@400&display=swap" rel="stylesheet">
<style>
:root{
  --blue:#1565c0;
  --blue-dark:#0d47a1;
  --navy:#1e2f4d;
  --navy-card:#102a5c;
  --red:#e52b2b;
  --red-form:#c8282f;
  --orange:#f7a41c;
  --orange-card:#f26b0f;
  --teal-card:#1e88c7;
  --green-card:#2e9e1c;
  --red-card:#ea1d2c;
  --amber-card:#d9890f;
  --ink:#333;
  --white:#fff;
}
*{box-sizing:border-box;margin:0;padding:0}
html,body{width:801px;height:1200px;overflow:hidden}
body{font-family:"Lato",sans-serif;color:var(--ink);background:var(--white);position:relative}
.abs{position:absolute}

/* header */
.site-header{position:absolute;left:0;top:0;width:801px;height:81px;background:var(--white)}
.brand{left:88px;top:18px;display:flex;align-items:center;gap:10px}
.brand-dot{width:44px;height:44px;border-radius:50%;background:var(--blue)}
.brand-name{font-weight:900;font-size:21px;color:var(--blue);letter-spacing:.2px;line-height:1}
.brand-tag{font-size:9.5px;letter-spacing:1px;color:#555;margin-top:5px;text-align:center}
.award{top:8px;width:110px;text-align:center;font-size:8.5px;font-weight:700;color:#222}
.award-badge{width:34px;height:50px;margin:0 auto 6px;background:linear-gradient(#f3c74a,#b68514);border-radius:4px 4px 17px 17px}
.phone{left:598px;top:34px;display:flex;align-items:center;gap:6px;color:var(--red);font-size:15.5px;font-weight:700}

/* nav */
.main-nav{position:absolute;left:0;top:81px;width:801px;height:31px;background:linear-gradient(#2c95e0,#0f64b5)}
.main-nav ul{list-style:none;display:flex;position:absolute;left:87px;top:0;height:31px;gap:12.5px}
.main-nav li{font-size:10px;font-weight:700;color:var(--white);line-height:31px;text-transform:uppercase;white-space:nowrap}
.main-nav li.active{border-bottom:2px solid var(--white);line-height:29px}

/* hero */
.hero{position:absolute;left:0;top:112px;width:801px;height:316px;background:linear-gradient(90deg,#7a3a1c 0%,#a85a30 8%,#d9d1c8 89%,#f0f0ee 100%)}
.video{left:87px;top:0;width:426px;height:240px;background:linear-gradient(160deg,#f4f4f4 0%,#e9e3de 45%,#e84a3a 75%,#f2cf2a 100%)}
.play{left:196px;top:102px;width:34px;height:22px;border-radius:5px;background:#e2424a}
.play::after{content:"";position:absolute;left:13px;top:5px;border-left:10px solid #fff;border-top:6px solid transparent;border-bottom:6px solid transparent}
.video-bar{left:87px;top:223px;width:426px;height:18px;background:linear-gradient(#3b3b3b,#111);display:flex;align-items:center;gap:6px;padding:0 6px;color:#ccc;font-size:6.5px}
.vb-btn{width:15px;height:10px;background:#4b6a9a;border-radius:2px}
.vb-track{width:126px;height:4px;background:#777;border-radius:2px;position:relative}
.vb-track::before{content:"";position:absolute;left:0;top:0;width:30px;height:4px;background:#ccc;border-radius:2px}
.hero-strip{left:87px;top:241px;width:426px;height:75px;background:var(--blue-dark);color:var(--white);font-family:"Oswald",sans-serif;font-size:11px;line-height:17px;padding:12px 0 0 14px}
.hero-strip b{color:var(--orange);font-weight:400}
.chamber{left:352px;top:15px;width:60px;height:42px;background:var(--navy);border:1px solid #fff}

.estimate{left:514px;top:0;width:200px;height:316px;background:var(--red-form);color:var(--white)}
.estimate-head{height:35px;background:linear-gradient(#fbb634,#e9900d);font-size:14px;font-weight:700;text-align:center;line-height:35px;letter-spacing:.3px}
.estimate h3{font-size:12.5px;text-align:center;margin-top:22px}
.estimate p{font-size:8.2px;line-height:11px;text-align:center;padding:0 12px;margin-top:5px}
.field{position:absolute;left:11px;width:177px;height:16px;background:#fff;border-radius:2px;font-size:8px;color:#333;padding:3px 6px}
.captcha-label{position:absolute;left:11px;top:241px;font-size:8px}
.btn-submit{position:absolute;left:11px;top:277px;width:87px;height:22px;border-radius:3px;background:linear-gradient(#f9b13a,#e68a0b);font-size:11px;font-weight:700;text-align:center;line-height:22px}
.estimate-dot{position:absolute;left:158px;top:282px;width:22px;height:22px;border-radius:50%;background:var(--blue)}

/* main */
.main{position:absolute;left:0;top:428px;width:801px;height:582px;background:linear-gradient(#e9f2fb,#c3daf2)}
.welcome{left:88px;top:22px;width:411px;height:231px;background:#fff;border:1px solid #b8cfe8;border-radius:7px;padding:15px 13px}
.welcome h1{font-size:13px;color:var(--blue-dark);font-weight:700;margin-bottom:5px}
.welcome h1 span{color:var(--red)}
.welcome p{font-size:9.8px;line-height:14.2px;color:#444;text-align:justify;margin-bottom:7px}
.btn-more{display:inline-block;background:#1d8fe0;color:#fff;font-size:9.5px;font-weight:700;padding:6px 7px;border-radius:2px}

.service{width:131px;height:94px;border-radius:4px;color:#fff;text-align:center}
.service-photo{position:absolute;left:34px;top:-35px;width:64px;height:64px;border-radius:50%;border:3px solid #fff;box-shadow:0 0 0 1px #888;background:linear-gradient(#c9c9c9,#7d7265)}
.service h4{font-size:9.6px;font-weight:700;text-transform:uppercase;margin-top:40px;white-space:nowrap}
.service p{font-size:8px;font-weight:700;line-height:11px;margin-top:4px}
.service .pill{position:absolute;left:37px;top:86px;width:58px;height:15px;background:#262626;border-radius:2px;font-size:8.5px;font-weight:700;line-height:15px}

/* sidebar */
.sidebar{left:514px;top:0;width:200px;height:582px;background:var(--navy)}
.side-head{position:absolute;left:0;top:22px;width:200px;height:23px;background:linear-gradient(#f8b637,#e08d0c);color:#fff;font-size:12px;font-weight:700;line-height:23px;padding:0 8px}
.side-head i{float:right;font-size:8.5px;color:#333;font-weight:700}
.t-person{position:absolute;left:13px;width:60px;height:60px;border-radius:50%;border:3px solid var(--orange);background:linear-gradient(#d8c3b4,#8f7a6c)}
.t-name{position:absolute;left:82px;font-size:9.5px;font-weight:700;color:var(--orange)}
.t-role{position:absolute;left:82px;font-size:8.5px;color:#ddd}
.t-quote{position:absolute;left:13px;width:175px;height:104px;background:#fff;border-radius:2px;padding:7px 8px;font-size:8.8px;font-style:italic;line-height:15px;color:#444;overflow:hidden}
.t-quote::before{content:"";position:absolute;left:45px;top:-8px;border-left:8px solid transparent;border-right:8px solid #fff;border-top:8px solid transparent}
.specials{position:absolute;left:0;top:460px;width:200px;height:94px;background:linear-gradient(90deg,#3f4a44,#8c8670 55%,#c2b9a2)}
.specials span{position:absolute;left:0;top:20px;width:200px;text-align:center;color:#fff;font-size:20px;font-weight:900;font-style:italic;line-height:26px}

/* footer */
.site-footer{position:absolute;left:0;top:1010px;width:801px;height:190px;background:var(--blue-dark);color:#fff}
.quick{left:88px;top:0;width:169px;height:190px;background:#f1f1f1}
.quick-head{height:27px;background:linear-gradient(#f8b637,#e08d0c);font-size:12px;font-weight:700;line-height:27px;padding-left:14px}
.quick ul{list-style:none;padding:9px 0 0 14px}
.quick li{font-size:9px;color:#222;line-height:16.8px;padding-left:19px;position:relative}
.quick li::before{content:"";position:absolute;left:0;top:5px;width:7px;height:7px;border-radius:50%;background:var(--blue)}
.f-title{font-size:12px;font-weight:700}
.email{left:282px;top:37px;width:209px;height:24px;background:#fff;color:#999;font-size:8px;line-height:24px;padding-left:7px}
.subscribe{left:496px;top:37px;width:56px;height:24px;background:var(--red);font-size:10.5px;line-height:24px;text-align:center}
.social{width:20px;height:20px;border-radius:50%;top:38px}
.f-rule{height:1px;background:#3f6fbd}
.f-text{font-size:9px;line-height:14px}
.bureau{left:600px;top:90px;width:115px;height:46px;background:#fff;border-radius:4px}
.bureau div{position:absolute;left:18px;top:8px;width:80px;height:30px;background:#0f5a90;border-radius:3px}
.copy{left:257px;top:167px;width:456px;text-align:center;font-size:8.5px;font-weight:700}
</style>
</head>
<body>

<header class="site-header">
  <div class="brand abs">
    <div class="brand-dot"></div>
    <div>
      <div class="brand-name">CORVEL COATINGS</div>
      <div class="brand-tag">COLOR DONE RIGHT, EVERY TIME</div>
    </div>
  </div>
  <div class="award abs" style="left:377px"><div class="award-badge" role="img" aria-label="Pellham Roster exterior award badge"></div>EXTERIOR PAINTING</div>
  <div class="award abs" style="left:467px"><div class="award-badge" role="img" aria-label="Pellham Roster interior award badge"></div>INTERIOR PAINTING</div>
  <div class="phone abs">
    <svg width="17" height="17" viewBox="0 0 20 20" aria-hidden="true"><circle cx="10" cy="10" r="9" fill="none" stroke="#1565c0" stroke-width="1.6"/><path d="M7 5.5l1.6 2.4-1 1.2c.7 1.4 1.7 2.4 3.1 3.1l1.2-1 2.4 1.6-.9 1.7c-3.6-.5-6.5-3.4-7.1-7.1z" fill="#1565c0"/></svg>
    555 010 4477
  </div>
</header>

<nav class="main-nav">
  <ul>
    <li class="active">Home</li><li>About Us</li><li>Residential Painting</li><li>Commercial Painting</li><li>FAQ</li><li>Specials</li><li>Blog</li><li>Testimonials</li><li>Contact Us</li>
  </ul>
</nav>

<section class="hero" role="img" aria-label="Freshly painted room interior with orange wall and bright window">
  <div class="video abs" role="img" aria-label="Video still: paint roller, tray and yellow paint bucket"></div>
  <div class="play abs"></div>
  <div class="video-bar abs"><span class="vb-btn"></span><span class="vb-track"></span><span>1:47 / 12:35</span><span style="flex:1"></span><span class="vb-btn"></span><span class="vb-btn"></span><span class="vb-btn"></span></div>
  <div class="hero-strip abs">
    Need Painting In The Albuquerque Area?<br>
    Call Dale Today For Your FREE Painting Estimate! <b>555-0148</b><br>
    Licensed - Bonded - Insured
    <div class="chamber abs" role="img" aria-label="Albuquerque Trade Council member badge"></div>
  </div>

  <form class="estimate abs">
    <div class="estimate-head">SCHEDULE FREE ESTIMATE</div>
    <h3>How to Schedule an Estimae</h3>
    <p>Requesting an estimate online is very simple and easy. Fill out the Form below and we will send you a rough quote to your email. We may also call you if we have any more questions.</p>
    <div class="field" style="top:131px">Name:</div>
    <div class="field" style="top:153px">Email:</div>
    <div class="field" style="top:175px">Phone:</div>
    <div class="field" style="top:197px;height:38px">Decribe what needs to be done.</div>
    <div class="captcha-label">Please type the following</div>
    <div class="field" style="top:254px">ac2gH</div>
    <div class="btn-submit">Submit Now</div>
    <div class="estimate-dot"></div>
  </form>
</section>

<main class="main">
  <article class="welcome abs">
    <h1>Welcome To CORVEL <span>COATINGS</span></h1>
    <p>Corvel Coatings does jobs as small as a bathroom up to large commercial projects right here in Albuquerque and Rio Rancho. Extensive as an entire apartment exterior, to a kitchen and all home interior, no job is too big or too small for Corvel Coatings of Albuquerque. Corvel Coatings is staffed with the best painters for the highest quality paint jobs. Corvel Coatings is not a community's average house painter staffing company, but this painting company is staffed with professional painters that pride themselves on successfully completing every job.</p>
    <p>Dale Mercer, owner of Corvel Coatings, Inc., started painting in 1975 during high school. He continued painting through college where he earned a Bachelor of Science degree from Prairie State University in 1984. Dale opened his first painting company in 1984.</p>
    <span class="btn-more">Read More</span>
  </article>

  <div class="service abs" style="left:87px;top:307px;background:var(--orange-card)"><div class="service-photo" role="img" aria-label="Commercial interior photo"></div><h4>Commercial Painting</h4><p>Lorem ipsum dolor sit amet,<br>consectetuer adipiscing</p><div class="pill">Read more</div></div>
  <div class="service abs" style="left:228px;top:307px;background:var(--teal-card)"><div class="service-photo" role="img" aria-label="House exterior photo"></div><h4>Residential Painting</h4><p>Lorem ipsum dolor sit amet,<br>consectetuer adipiscing</p><div class="pill">Read more</div></div>
  <div class="service abs" style="left:369px;top:307px;background:var(--green-card)"><div class="service-photo" role="img" aria-label="Stucco wall photo" style="background:linear-gradient(#a66a4a,#5a3a2c)"></div><h4>Stucco Coatings</h4><p>Lorem ipsum dolor sit amet,<br>consectetuer adipiscing</p><div class="pill">Read more</div></div>
  <div class="service abs" style="left:87px;top:460px;background:var(--navy-card)"><div class="service-photo" role="img" aria-label="Kitchen cabinets photo"></div><h4>Cabinets</h4><p>Lorem ipsum dolor sit amet,<br>consectetuer adipiscing</p><div class="pill">Read more</div></div>
  <div class="service abs" style="left:228px;top:460px;background:var(--red-card)"><div class="service-photo" role="img" aria-label="Lit house at dusk photo" style="background:linear-gradient(#4a3a30,#d08a40)"></div><h4>Interior/ Exterior</h4><p>Lorem ipsum dolor sit amet,<br>consectetuer adipiscing</p><div class="pill">Read more</div></div>
  <div class="service abs" style="left:369px;top:460px;background:var(--amber-card)"><div class="service-photo" role="img" aria-label="Drywall texture photo" style="background:linear-gradient(#e8e2d8,#b9a58a)"></div><h4>Dry Wall Texture Repair</h4><p>Lorem ipsum dolor sit amet,<br>consectetuer adipiscing</p><div class="pill">Read more</div></div>

  <aside class="sidebar abs">
    <div class="side-head">Testimonials <i>View All</i></div>
    <div class="t-person" style="top:54px" role="img" aria-label="Customer portrait"></div>
    <div class="t-name" style="top:72px">Tomas Verlane</div>
    <div class="t-role" style="top:86px">Lorem Ipsum</div>
    <div class="t-quote" style="top:122px">“ Ut wisi enim ad minim veniam, quism nostrli erci tation ullamcorper suscipitop lobortis commodo consequat Ut wisi enim ad minim veniam, quism nostrli erci tation ullamcorper suscipitop lobortis commodo consequat. ”</div>
    <div class="t-person" style="top:236px" role="img" aria-label="Customer portrait"></div>
    <div class="t-name" style="top:255px">Tomas Verlane</div>
    <div class="t-role" style="top:269px">Lorem Ipsum</div>
    <div class="t-quote" style="top:305px">“ Ut wisi enim ad minim veniam, quism nostrli erci tation ullamcorper suscipitop lobortis commodo consequat Ut wisi enim ad minim veniam, quism nostrli erci tation ullamcorper suscipitop lobortis commodo consequat. ”</div>
    <div class="specials" role="img" aria-label="Furnished living room photo"><span>Check Out<br>Our Specials!</span></div>
  </aside>
</main>

<footer class="site-footer">
  <nav class="quick abs">
    <div class="quick-head">Quick Links</div>
    <ul><li>HOME</li><li>ABOUT US</li><li>RESIDENTIAL PAINTING</li><li>COMMERCIAL PAINTING</li><li>FAQ</li><li>SPECIALS</li><li>BLOG</li><li>TESTIMONIALS</li><li>CONTACT US</li></ul>
  </nav>
  <div class="f-title abs" style="left:283px;top:15px">Sign up for Newsletter</div>
  <div class="email abs">Enter Your Email</div>
  <div class="subscribe abs">SUBMIT</div>
  <div class="abs f-rule" style="left:576px;top:18px;width:1px;height:50px"></div>
  <div class="f-title abs" style="left:601px;top:15px">Follow Us On</div>
  <div class="social abs" style="left:600px;background:#3a6fb0" role="img" aria-label="Social profile link one"></div>
  <div class="social abs" style="left:627px;background:#2f8fc8" role="img" aria-label="Social profile link two"></div>
  <div class="social abs" style="left:654px;background:#2a6a98" role="img" aria-label="Social profile link three"></div>
  <div class="social abs" style="left:681px;background:#c8453a" role="img" aria-label="Social profile link four"></div>
  <div class="abs f-rule" style="left:282px;top:78px;width:432px"></div>

  <svg class="abs" style="left:282px;top:94px" width="10" height="14" viewBox="0 0 10 14" aria-hidden="true"><path d="M5 0a5 5 0 0 1 5 5c0 3.5-5 9-5 9S0 8.5 0 5a5 5 0 0 1 5-5z" fill="#fff"/><circle cx="5" cy="5" r="2" fill="#0d47a1"/></svg>
  <div class="abs f-text" style="left:300px;top:95px">Corvel Coatings Inc.<br>4120 Larkmoor Road Northeast,<br>Albuquerque, NM 87190</div>
  <svg class="abs" style="left:470px;top:96px" width="8" height="12" viewBox="0 0 8 12" aria-hidden="true"><rect x=".5" y=".5" width="7" height="11" rx="1" fill="none" stroke="#fff"/><rect x="2" y="2" width="4" height="6" fill="#fff"/></svg>
  <div class="abs f-text" style="left:488px;top:95px;font-size:10px">555-933-0172</div>
  <svg class="abs" style="left:436px;top:121px" width="11" height="8" viewBox="0 0 11 8" aria-hidden="true"><rect x=".5" y=".5" width="10" height="7" fill="none" stroke="#fff"/><path d="M.5.5l5 4 5-4" fill="none" stroke="#fff"/></svg>
  <div class="abs f-text" style="left:454px;top:118px">info@corvelcoatings.example</div>
  <div class="abs f-rule" style="left:576px;top:92px;width:1px;height:45px"></div>
  <div class="bureau abs" role="img" aria-label="Trade bureau accreditation badge"><div></div></div>
  <div class="abs f-rule" style="left:282px;top:146px;width:432px"></div>
  <div class="copy abs">© 2015 CORVEL COATINGS. All Rights Reserved.</div>
</footer>

</body>
</html>
```